Rebrand & reskin fitbrisko.com (Uncoded)

Fitbrisko.com is a commerce website and app for sports and fitness classes and events. In order to improve its appeal, we invite designers to provide their 'skins' for the landing page, club page and event page. Designers can propose using alternate controls and layouts for these pages, and comment on ways to improve the site's usability. It must remain easy to use on a portrait mobile phone screen, responsive design where necessary to also provide a good experience on desktop.

Please navigate to fitbrisko.com and explore the site, and we look forwards to your suggestions!

Target Market(s)

Primary: Tech-savvy mobile users. Secondary: Desktop users

Industry/Entity Type

Health And Wellness

Number of Pages Required

3 page

Font styles to use
Sans Serif

Colors
ffffff
f37122

Requirements
Must have
• This brief is all about changing the look and feel of the site; the winning design will have an immediate 'wow' factor, yet not sacrifice the ease of finding and paying for classes. It must retain the logo, white and orange must be the primary colours used.
Should not have
• The colour palette must remain roughly as is; for example, a very dark site will not appeal.

```html
<!DOCTYPE html>
<html lang="en">
<head>
<meta charset="utf-8">
<title>Fitbrisko – Feed</title>
<link href="https://fonts.googleapis.com/css2?family=Roboto:wght@400;500;700&display=swap" rel="stylesheet">
<style>
:root{
  --orange:#f37122;
  --white:#ffffff;
  --page:#efefef;
  --dark:#252525;
  --darker:#1e1e1e;
  --black:#000000;
  --text:#333333;
  --muted:#777777;
  --line:#e2e2e2;
  --grey-date:#8d8d8d;
}
*{box-sizing:border-box;margin:0;padding:0}
html,body{width:1200px;height:1034px;overflow:hidden}
body{position:relative;background:var(--page);font-family:'Roboto',Arial,sans-serif;color:var(--text)}
.site-header{position:absolute;left:0;top:0;width:1200px;height:103px;background:var(--white);box-shadow:0 1px 4px rgba(0,0,0,.12)}
.brand{position:absolute;left:93px;top:34px;display:flex;align-items:center;gap:10px}
.brand-mark{width:30px;height:30px;border-radius:50%;background:var(--orange)}
.brand-name{font-weight:700;font-size:29px;color:var(--orange);letter-spacing:1px}
.main-nav{position:absolute;top:0;right:91px;height:103px;display:flex}
.main-nav a{display:flex;align-items:center;height:103px;padding:0 22px;font-size:15px;color:#444;text-decoration:none}
.main-nav a.active{background:var(--orange);color:var(--white);padding:0 22px}
.side-menu{position:absolute;left:88px;top:142px;width:228px;height:747px;background:var(--dark)}
.side-item{display:flex;height:46px;border-bottom:1px solid #333;color:var(--white);font-size:16px}
.side-item .ico{width:62px;display:flex;align-items:center;justify-content:center;background:var(--darker)}
.side-item .label{flex:1;display:flex;align-items:center;justify-content:space-between;padding:0 16px 0 14px}
.side-item.active,.side-item.active .ico{background:var(--orange)}
.side-item.active .ico{background:#e8661a}
.hero{position:absolute;left:349px;top:142px;width:764px;height:266px;background:var(--white);padding:3px;box-shadow:0 1px 3px rgba(0,0,0,.15)}
.hero-photo{width:100%;height:100%;background:linear-gradient(180deg,#1e3d78 0%,#35588e 45%,#5a7a55 80%,#4d6b3c 100%);display:flex;flex-direction:column;align-items:center;justify-content:center;color:var(--white);text-align:center}
.hero h1{font-size:32px;font-weight:700;margin-bottom:10px;text-shadow:0 1px 3px rgba(0,0,0,.5)}
.hero p{font-size:15px;line-height:21px;text-shadow:0 1px 2px rgba(0,0,0,.5)}
.panel{position:absolute;top:433px;background:var(--white);box-shadow:0 1px 3px rgba(0,0,0,.15)}
.panel-head{height:45px;background:var(--orange);color:var(--white);font-size:18px;font-weight:500;display:flex;align-items:center;padding:0 21px}
.classes{left:349px;width:418px;height:456px}
.events{left:780px;width:334px;height:456px}
.class-row{display:flex;align-items:center;height:102px;border-bottom:1px solid var(--line);padding:0 19px}
.class-row:last-child{border-bottom:none}
.badge{width:64px;height:64px;border-radius:4px;flex:none;margin-right:16px}
.badge.maroon{background:#7c1414}
.badge.black{background:#1a1a1a}
.class-title{font-size:11px;color:var(--orange);text-transform:uppercase;margin-bottom:7px}
.class-desc{font-size:11px;color:#555;margin-bottom:8px}
.class-date{font-size:11px;color:#333;display:flex;align-items:center;gap:9px}
.event-row{display:flex;height:100px;border-bottom:1px solid var(--line);padding:17px 20px 0 20px}
.event-row:last-child{border-bottom:none}
.date-box{width:40px;flex:none;margin-right:15px;text-align:center;color:var(--white)}
.date-top{background:var(--grey-date);height:40px;padding-top:4px}
.date-top .day{font-size:17px;line-height:18px}
.date-top .mon{font-size:8px;margin-top:4px}
.date-year{background:#2b2b2b;height:35px;line-height:35px;font-size:11px;font-weight:500}
.event-title{font-size:12px;color:#222;text-transform:uppercase;margin-bottom:6px}
.event-text{font-size:10.5px;color:#777;line-height:17px;text-align:justify}
.event-more{font-size:11px;color:var(--orange);margin-top:3px}
.site-footer{position:absolute;left:0;top:926px;width:1200px;height:108px;background:var(--black);color:var(--white)}
.footer-links{position:absolute;left:98px;top:33px;font-size:14px}
.footer-links span{margin:0 8px}
.copyright{position:absolute;left:99px;top:60px;font-size:14px}
.social{position:absolute;right:91px;top:35px;display:flex;gap:9px}
.social span{width:34px;height:34px;border-radius:3px;background:var(--orange)}
</style>
</head>
<body>
<header class="site-header">
  <div class="brand"><span class="brand-mark"></span><span class="brand-name">FITBRISKO</span></div>
  <nav class="main-nav">
    <a href="#">CALENDAR</a><a href="#" class="active">FEED</a><a href="#">NEARBY</a><a href="#">SPORTS</a><a href="#">FITNESS</a><a href="#">EVENTS</a>
  </nav>
</header>

<aside class="side-menu">
  <div class="side-item active"><span class="ico"><svg width="18" height="18" viewBox="0 0 18 18"><rect x="2" y="2" width="9" height="12" fill="#fff"/><rect x="7" y="6" width="9" height="11" fill="#fff" stroke="#e8661a"/></svg></span><span class="label">My Diary<svg width="8" height="12" viewBox="0 0 8 12"><path d="M1 1l5 5-5 5" stroke="#fff" stroke-width="2" fill="none"/></svg></span></div>
  <div class="side-item"><span class="ico"><svg width="18" height="16" viewBox="0 0 18 16"><path d="M9 1L1 8h2v7h4v-4h4v4h4V8h2z" fill="#fff"/></svg></span><span class="label">My Clubs<svg width="8" height="12" viewBox="0 0 8 12"><path d="M1 1l5 5-5 5" stroke="#fff" stroke-width="2" fill="none"/></svg></span></div>
  <div class="side-item"><span class="ico"><svg width="16" height="17" viewBox="0 0 16 17"><circle cx="8" cy="5" r="4" fill="#fff"/><path d="M1 16c0-5 3-7 7-7s7 2 7 7z" fill="#fff"/></svg></span><span class="label">My Profile<svg width="8" height="12" viewBox="0 0 8 12"><path d="M1 1l5 5-5 5" stroke="#fff" stroke-width="2" fill="none"/></svg></span></div>
  <div class="side-item"><span class="ico"><svg width="18" height="16" viewBox="0 0 18 16"><path d="M1 6h6V2l6 6-6 6v-4H1z" fill="#fff"/><path d="M11 1h5v14h-5" stroke="#fff" stroke-width="2" fill="none"/></svg></span><span class="label">Login<svg width="8" height="12" viewBox="0 0 8 12"><path d="M1 1l5 5-5 5" stroke="#fff" stroke-width="2" fill="none"/></svg></span></div>
</aside>

<section class="hero">
  <div class="hero-photo" role="img" aria-label="Photo of a sprinter starting a race on a stadium track">
    <h1>WELCOME TO FITBRISKO</h1>
    <p>Thanks for visiting! Here are a list of events that we hope are of interest.<br>Just click on the grey tick to join an event, or Login</p>
  </div>
</section>

<section class="panel classes">
  <div class="panel-head">SPORTS AND FITNESS CLASSES</div>
  <div class="class-row"><span class="badge maroon"></span><div><div class="class-title">North Ridge Runners @ Elmfield School</div><div class="class-desc">Freestyle (crawl) training comprising of warm up, drills and</div><div class="class-date"><svg width="10" height="10" viewBox="0 0 10 10"><rect x="0.5" y="1.5" width="9" height="8" fill="none" stroke="#f37122"/><rect x="0.5" y="1.5" width="9" height="2.5" fill="#f37122"/></svg>MONDAY&nbsp; 20/01/2016</div></div></div>
  <div class="class-row"><span class="badge black"></span><div><div class="class-title">North Ridge Runners @ Elmfield School</div><div class="class-desc">Freestyle (crawl) training comprising of warm up, drills and</div><div class="class-date"><svg width="10" height="10" viewBox="0 0 10 10"><rect x="0.5" y="1.5" width="9" height="8" fill="none" stroke="#f37122"/><rect x="0.5" y="1.5" width="9" height="2.5" fill="#f37122"/></svg>MONDAY&nbsp; 20/01/2016</div></div></div>
  <div class="class-row"><span class="badge maroon"></span><div><div class="class-title">North Ridge Runners @ Elmfield School</div><div class="class-desc">Freestyle (crawl) training comprising of warm up, drills and</div><div class="class-date"><svg width="10" height="10" viewBox="0 0 10 10"><rect x="0.5" y="1.5" width="9" height="8" fill="none" stroke="#f37122"/><rect x="0.5" y="1.5" width="9" height="2.5" fill="#f37122"/></svg>MONDAY&nbsp; 20/01/2016</div></div></div>
  <div class="class-row"><span class="badge black"></span><div><div class="class-title">North Ridge Runners @ Elmfield School</div><div class="class-desc">Freestyle (crawl) training comprising of warm up, drills and</div><div class="class-date"><svg width="10" height="10" viewBox="0 0 10 10"><rect x="0.5" y="1.5" width="9" height="8" fill="none" stroke="#f37122"/><rect x="0.5" y="1.5" width="9" height="2.5" fill="#f37122"/></svg>MONDAY&nbsp; 20/01/2016</div></div></div>
</section>

<section class="panel events">
  <div class="panel-head">EVENTS</div>
  <div class="event-row"><div class="date-box"><div class="date-top"><div class="day">02</div><div class="mon">JUN</div></div><div class="date-year">2016</div></div><div><div class="event-title">North Ridge Runners</div><div class="event-text">Lorem Ipsum has been the industry's standard dummy text ever since the 1500s, when unknown</div><div class="event-more">View More »</div></div></div>
  <div class="event-row"><div class="date-box"><div class="date-top"><div class="day">02</div><div class="mon">JUN</div></div><div class="date-year">2016</div></div><div><div class="event-title">North Ridge Runners</div><div class="event-text">Lorem Ipsum has been the industry's standard dummy text ever since the 1500s, when unknown</div><div class="event-more">View More »</div></div></div>
  <div class="event-row"><div class="date-box"><div class="date-top"><div class="day">02</div><div class="mon">JUN</div></div><div class="date-year">2016</div></div><div><div class="event-title">North Ridge Runners</div><div class="event-text">Lorem Ipsum has been the industry's standard dummy text ever since the 1500s, when unknown</div><div class="event-more">View More »</div></div></div>
  <div class="event-row"><div class="date-box"><div class="date-top"><div class="day">02</div><div class="mon">JUN</div></div><div class="date-year">2016</div></div><div><div class="event-title">North Ridge Runners</div><div class="event-text">Lorem Ipsum has been the industry's standard dummy text ever since the 1500s, when unknown</div><div class="event-more">View More »</div></div></div>
</section>

<footer class="site-footer">
  <div class="footer-links">Privacy Policy<span>|</span>Terms of Use<span>|</span>About Us<span>|</span>Sitemap</div>
  <div class="copyright">Copyright © 2016&nbsp; All Rights</div>
  <div class="social"><span></span><span></span><span></span><span></span></div>
</footer>
</body>
</html>
```